Quality Monitoring Company Needs a New Site

We are an established company that has a fair number of clients but the site lacks current design standards that we'd like to keep up with. We'd like to mimic the same style of the site on plinkora.com, vetrumo.com, https://brindlecoffer.com/, etc. We'd also like to make sure the designer understands SEO Silos and how it effects the design elements. Attached is the structure that I'd like to follow for the pages. You don't need to design every single sub-page because they'll probably be fairly similar; however, I want to see at least 1 each. Please use the content on our current site for filler areas. Please try to do a good job of understanding what we do so you can use your best judgement on what is needed to be successful. Use our color scheme and the logo should be the side view but I included the AI just in case.
Updates

I am narrowing down on the field of designs that I have received. There are a lot of similarities between the designs I like and don't like. I'd also like to ensure that some of the inner pages get done in the next 5 days so I can see the creativity that is there as well. That is probably what is next -- getting a few inner pages completed so I can see what you can come up with (not based on our current website) because the current "front pages" are all so good and so close.

Industry/Entity Type

Telecommunications

Colors

Designer to choose colors to be used in the design.

Requirements
Must have
• SEO Silo Look and Feel
• Current Colors
Should not have
• No stockphotos whatsoever. NONE.

```html
<!DOCTYPE html>
<html lang="en">
<head>
<meta charset="utf-8">
<title>Tellmark — Call Center Quality Assurance</title>
<link rel="stylesheet" href="https://fonts.googleapis.com/css2?family=Josefin+Sans:wght@600;700&family=Lato:wght@400;700;900&display=swap">
<style>
:root{
  --navy:#0c1a3d;
  --blue:#1a8fd6;
  --sky:#dff0fb;
  --text:#1d2333;
  --muted:#9aa0ab;
  --line:#e6e8ec;
  --footer:#151b2d;
  --panel:#efeff1;
  --white:#fff;
}
*{box-sizing:border-box;margin:0;padding:0}
html,body{width:1200px;height:4376px;overflow:hidden;background:var(--white)}
body{position:relative;font-family:'Lato',sans-serif;color:var(--text)}
.abs{position:absolute}
.wordmark{font-family:'Lato',sans-serif;font-weight:700;color:var(--navy);font-size:40px;letter-spacing:-.5px}
.nav{position:absolute;top:52px;left:420px;display:flex;gap:22px;align-items:center;font-size:14px;font-weight:700;color:var(--navy)}
.nav .active{color:var(--blue);position:relative}
.nav .active::after{content:"";position:absolute;left:-6px;right:-6px;bottom:-10px;height:2px;background:var(--blue)}
.btn{display:inline-flex;align-items:center;gap:6px;border-radius:22px;font-weight:900;font-size:13px;color:#fff;background:var(--blue);box-shadow:0 6px 14px rgba(26,143,214,.3)}
.btn .dot{width:10px;height:10px;border-radius:50%;background:#fff}
.btn-auth{position:absolute;left:942px;top:44px;padding:11px 16px;font-size:15px}
.hero-h{position:absolute;left:145px;top:244px;font-family:'Josefin Sans',sans-serif;font-weight:700;font-size:32px;line-height:43px;color:var(--navy)}
.hero-h .b{color:var(--blue)}
.hero-btn{position:absolute;left:145px;top:446px;padding:9px 22px}
.dots{position:absolute;left:145px;top:533px;display:flex;gap:10px}
.dots i{width:10px;height:10px;border-radius:50%;background:#a3a7ae}
.dots i.on{background:var(--blue)}
.sec-title{position:absolute;left:0;width:1200px;text-align:center;font-family:'Josefin Sans',sans-serif;font-weight:700;font-size:46px;color:var(--navy)}
.sec-title span{color:var(--blue)}
.service{position:absolute;width:300px;text-align:center}
.service .ico{width:86px;height:86px;margin:0 auto 16px;border-radius:18px;background:linear-gradient(135deg,#e3f1fb,#c7e2f5)}
.service h3{font-size:18px;font-weight:700;color:var(--navy);margin-bottom:10px}
.service p{font-size:13.5px;line-height:27px;color:var(--muted)}
.service .btn{margin-top:14px;padding:10px 20px}
.service.card{background:#fff;border-radius:24px;box-shadow:0 10px 30px rgba(12,26,61,.12);padding:40px 18px 0;height:393px}
.arrow{position:absolute;width:30px;height:30px;border-radius:50%;border:1.5px solid #c9ccd2;display:flex;align-items:center;justify-content:center;color:#b1b5bc;font-size:14px;background:#fff}
.ind{position:absolute;width:340px}
.ind h4{font-size:20px;font-weight:700;color:var(--navy)}
.ind p{font-size:12px;line-height:21px;color:var(--muted);margin-top:6px}
.ind.l{text-align:right}
.ind .badge{position:absolute;top:-6px;width:72px;height:72px;border-radius:50%;background:#fff;box-shadow:0 6px 18px rgba(12,26,61,.12);display:flex;align-items:center;justify-content:center}
.ind .badge i{width:38px;height:38px;border-radius:10px;background:linear-gradient(135deg,#f7b84a,#e5574d)}
.ind.l .badge{right:-100px}
.ind.r .badge{left:-100px}
.price{position:absolute;top:2256px;width:294px;background:#fff;box-shadow:0 8px 24px rgba(12,26,61,.1)}
.price .head{height:37px;background:var(--navy);color:#fff;text-align:center;font-weight:700;font-size:19px;line-height:37px}
.price.gold .head{background:var(--blue)}
.price .amt{text-align:center;padding:18px 0 16px;font-size:11px;color:var(--muted);border-bottom:1px solid var(--line)}
.price .amt b{font-size:25px;color:var(--text);font-weight:900}
.price .trial{margin:14px 12px 0;background:var(--panel);text-align:center;padding:16px 0 14px}
.price .trial strong{display:block;color:var(--blue);font-size:18px;font-weight:400;margin-bottom:8px}
.price .trial span{font-size:13px}
.price ul{list-style:none;padding:26px 0 0 32px}
.price li{font-size:13px;color:#5b616c;margin-bottom:19px;display:flex;align-items:center;gap:14px}
.price li::before{content:"";width:11px;height:11px;border-radius:50%;border:2.5px solid var(--blue);box-sizing:border-box}
.price.gold li::before{border-color:var(--navy)}
.price .sign{position:absolute;left:50%;transform:translateX(-50%);padding:10px 32px;background:var(--navy);color:#fff;border-radius:20px;font-size:12px;font-weight:900;display:flex;gap:6px;align-items:center;white-space:nowrap}
.price .sign .dot{width:9px;height:9px;border-radius:50%;background:#fff}
.member{position:absolute;top:3102px;width:236px;text-align:center}
.member .av{width:136px;height:136px;border-radius:50%;margin:0 auto 22px;background:linear-gradient(160deg,#f4f5f7,#e4e6ea);box-shadow:0 4px 14px rgba(12,26,61,.08)}
.member h5{font-size:18px;font-weight:400;color:var(--navy)}
.member p{font-size:13px;line-height:22px;color:var(--muted);margin-top:10px}
.member .soc{display:flex;justify-content:center;gap:26px;margin-top:16px}
.member .soc i{width:12px;height:12px;border-radius:50%;background:var(--blue)}
.post{position:absolute;top:3680px;width:279px;height:186px;border:2px solid #dcdee2;background:#fff;padding:20px 20px 0}
.post.mid{box-shadow:0 6px 18px rgba(12,26,61,.16)}
.post .date{position:absolute;left:20px;top:20px;width:44px;height:42px;background:var(--navy);color:#fff;text-align:center;line-height:15px;padding-top:5px}
.post .date b{font-size:20px;display:block}
.post .date small{font-size:11px;font-weight:700}
.post h6{margin-left:62px;font-size:15px;line-height:22px;font-weight:700;color:var(--navy)}
.post p{font-size:11.5px;line-height:19px;color:var(--muted);margin-top:18px}
.post a{display:block;margin-top:8px;font-size:13px;font-weight:700;color:var(--blue);text-decoration:none}
.footer-contact{position:absolute;top:4152px;left:0;width:1200px;display:flex;justify-content:center;gap:40px;color:#fff;font-size:13.5px;align-items:center}
.footer-contact .it{display:flex;align-items:center;gap:14px}
.footer-contact .ci{width:42px;height:42px;border-radius:50%;border:2px solid #fff;display:flex;align-items:center;justify-content:center}
.footer-contact .ci.fill{background:var(--blue);border-color:var(--blue)}
.footer-nav{position:absolute;top:4227px;width:1200px;display:flex;justify-content:center;gap:26px;color:#fff;font-size:17px}
.copy{position:absolute;top:4271px;width:1200px;text-align:center;color:#fff;font-size:12px}
.social{position:absolute;top:4313px;width:1200px;display:flex;justify-content:center;gap:10px}
.social i{width:26px;height:26px;border-radius:50%;background:var(--blue)}
</style>
</head>
<body>

<header>
  <div class="abs wordmark" style="left:144px;top:38px">Tellmark</div>
  <nav class="nav">
    <span class="active">Home</span><span>Services</span><span>Industries</span><span>Pricing</span><span>Team</span><span>Contact us</span><span>Blog</span>
    <svg width="16" height="16" viewBox="0 0 16 16"><circle cx="6.5" cy="6.5" r="4.5" fill="none" stroke="#0c1a3d" stroke-width="2"/><path d="M10 10l4 4" stroke="#0c1a3d" stroke-width="2"/></svg>
  </nav>
  <span class="btn btn-auth">USER AUTH</span>
</header>

<section class="hero">
  <h1 class="hero-h">We are an affordable,<br><span class="b">Accurate, and fully scalable</span><br>Call Center Quality<br><span class="b">Assurance Agency</span></h1>
  <span class="btn hero-btn">GET STARTED <span class="dot"></span></span>
  <div class="dots"><i></i><i></i><i class="on"></i><i></i><i></i></div>
  <div class="abs" role="img" aria-label="Illustration of an agent working at a curved desk with a plant" style="left:697px;top:115px;width:476px;height:500px;border-radius:48% 52% 40% 60%/45% 40% 60% 55%;background:linear-gradient(160deg,#e2f2fc 0%,#dcdbe8 60%,#4f4a6b 100%)"></div>
</section>

<svg class="abs" style="left:0;top:660px" width="1200" height="720" viewBox="0 660 1200 720" aria-hidden="true">
  <defs><filter id="sh" x="-10%" y="-10%" width="120%" height="130%"><feDropShadow dx="0" dy="10" stdDeviation="12" flood-color="#0c1a3d" flood-opacity=".1"/></filter></defs>
  <path d="M60 830 Q60 680 210 676 L990 772 Q1140 790 1140 920 L1140 1150 Q1140 1262 1010 1276 L220 1360 Q60 1376 60 1220 Z" fill="#fff" filter="url(#sh)"/>
</svg>

<section class="services">
  <h2 class="sec-title" style="top:780px">Our <span>Services</span></h2>
  <div class="arrow" style="left:91px;top:1052px">‹</div>
  <div class="arrow" style="left:1079px;top:1052px">›</div>
  <div class="service" style="left:119px;top:900px">
    <div class="ico" role="img" aria-label="Shield and gear icon"></div>
    <h3>QUALITY ASSURANCE</h3>
    <p>Sed ut perspiciatis unde omnis iste natus error sit voluptatem accuium doloremque laudantium, totam rem aperiam, eaque ipsa quae</p>
    <span class="btn">READ MORE</span>
  </div>
  <div class="service card" style="left:452px;top:870px">
    <div class="ico" role="img" aria-label="Coach and trainee icon"></div>
    <h3>COACHING</h3>
    <p>Sed ut perspiciatis unde omnis iste natus error sit voluptatem accuium doloremque laudantium, totam rem aperiam, eaque ipsa quae</p>
    <span class="btn">READ MORE</span>
  </div>
  <div class="service" style="left:782px;top:900px">
    <div class="ico" role="img" aria-label="Hand holding percent icon"></div>
    <h3>SALES PERFORMANCE</h3>
    <p>Sed ut perspiciatis unde omnis iste natus error sit voluptatem accuium doloremque laudantium, totam rem aperiam, eaque ipsa quae</p>
    <span class="btn">READ MORE</span>
  </div>
</section>

<section class="industries">
  <h2 class="sec-title" style="top:1430px">Our <span>Industries</span></h2>
  <div class="ind l" style="left:0;top:1550px;width:330px"><h4>Education</h4><p>Sed ut perspiciatis unde omnis iste<br>natus error sit voluptatem</p><span class="badge"><i></i></span></div>
  <div class="ind l" style="left:0;top:1671px;width:330px"><h4>Insurance</h4><p>Sed ut perspiciatis unde omnis iste<br>natus error sit voluptatem</p><span class="badge"><i></i></span></div>
  <div class="ind l" style="left:0;top:1791px;width:330px"><h4>Mortgage</h4><p>Sed ut perspiciatis unde omnis iste<br>natus error sit voluptatem</p><span class="badge"><i></i></span></div>
  <div class="ind l" style="left:0;top:1911px;width:377px"><h4>Automotive</h4><p>Sed ut perspiciatis unde omnis iste<br>natus error sit voluptatem</p><span class="badge"><i style="border-radius:50%;background:linear-gradient(135deg,#8a8f9c,#3e4456)"></i></span></div>
  <div class="ind r" style="left:870px;top:1550px"><h4>Utilities</h4><p>Sed ut perspiciatis unde omnis iste<br>natus error sit voluptatem</p><span class="badge"><i></i></span></div>
  <div class="ind r" style="left:870px;top:1671px"><h4>Financial Services</h4><p>Sed ut perspiciatis unde omnis iste<br>natus error sit voluptatem</p><span class="badge"><i style="background:linear-gradient(135deg,#e8edf2,#9aa7b5)"></i></span></div>
  <div class="ind r" style="left:870px;top:1791px"><h4>Home Services</h4><p>Sed ut perspiciatis unde omnis iste<br>natus error sit voluptatem</p><span class="badge"><i></i></span></div>
  <div class="ind r" style="left:870px;top:1911px"><h4>Call Tracking</h4><p>Sed ut perspiciatis unde omnis iste<br>natus error sit voluptatem</p><span class="badge"><i style="background:linear-gradient(135deg,#f5c64a,#1a8fd6)"></i></span></div>
  <div class="abs" role="img" aria-label="Illustration of a smartphone showing a voice recording with a person beside it" style="left:434px;top:1655px;width:331px;height:228px;border-radius:40% 46% 12% 18%/50% 44% 14% 20%;background:linear-gradient(180deg,#d6ebf9,#bfe0f6)"></div>
  <div class="abs" style="left:143px;top:2088px;width:914px;height:1px;background:var(--line)"></div>
</section>

<section class="pricing">
  <h2 class="sec-title" style="top:2165px">Our <span>Pricing</span></h2>
  <div class="price" style="left:143px;height:444px">
    <div class="head">FREE</div>
    <div class="amt">$99.99<b>49.99</b>/ per Month*</div>
    <div class="trial"><strong>Start Free Trial Now</strong><span>Free for 14 Days</span></div>
    <ul><li>Lorem ipsum dolor sit amet</li><li>Consectetur adipiscing elit</li><li>Sed do eiusmod tempor</li><li>Incididunt ut labore etdolore</li><li>Magna aliquanim ad minim</li></ul>
    <span class="sign" style="top:427px">SIGN UP <span class="dot"></span></span>
  </div>
  <div class="price gold" style="left:454px;height:498px">
    <div class="head">GOLD</div>
    <div class="amt">$99.99<b>59.99</b>/ per Month*</div>
    <div class="trial"><strong>Start Free Trial Now</strong><span>Free for 11 Days</span></div>
    <ul><li>Lorem ipsum dolor sit amet</li><li>Consectetur adipiscing elit</li><li>Sed do eiusmod tempor</li><li>Incididunt ut labore etdolore</li><li>Magna aliquanim ad minim</li><li>Nemo enim ipsam voluptatem</li></ul>
    <span class="sign" style="top:479px">SIGN UP <span class="dot"></span></span>
  </div>
  <div class="price" style="left:763px;height:444px">
    <div class="head">PLATINUM</div>
    <div class="amt">$99.99<b>69.99</b>/ per Month*</div>
    <div class="trial"><strong>Start Free Trial Now</strong><span>Free for 21 Days</span></div>
    <ul><li>Lorem ipsum dolor sit amet</li><li>Consectetur adipiscing elit</li><li>Sed do eiusmod tempor</li><li>Incididunt ut labore etdolore</li><li>Magna aliquanim ad minim</li></ul>
    <span class="sign" style="top:427px">SIGN UP <span class="dot"></span></span>
  </div>
</section>

<svg class="abs" style="left:0;top:2830px" width="1200" height="730" viewBox="0 2830 1200 730" aria-hidden="true">
  <defs><filter id="sh2" x="-10%" y="-10%" width="120%" height="130%"><feDropShadow dx="0" dy="10" stdDeviation="12" flood-color="#0c1a3d" flood-opacity=".1"/></filter></defs>
  <path d="M60 3000 Q60 2850 210 2848 L1000 2940 Q1140 2958 1140 3090 L1140 3330 Q1140 3436 1010 3452 L220 3534 Q60 3550 60 3390 Z" fill="#fff" filter="url(#sh2)"/>
</svg>

<section class="team">
  <h2 class="sec-title" style="top:2995px">Our <span>Team</span></h2>
  <div class="arrow" style="left:91px;top:3222px">‹</div>
  <div class="arrow" style="left:1079px;top:3222px">›</div>
  <div class="member" style="left:127px"><div class="av" role="img" aria-label="Avatar illustration of a team member"></div><h5>JOHN DOE</h5><p>Sed ut perspiciatis unde omnis iste<br>natus error sit voluptatem</p><div class="soc"><i></i><i></i><i></i></div></div>
  <div class="member" style="left:363px"><div class="av" role="img" aria-label="Avatar illustration of a team member"></div><h5>NELA PARSONS</h5><p>Sed ut perspiciatis unde omnis iste<br>natus error sit voluptatem</p><div class="soc"><i></i><i></i><i></i></div></div>
  <div class="member" style="left:599px"><div class="av" role="img" aria-label="Avatar illustration of a team member"></div><h5>ORIN VALE</h5><p>Sed ut perspiciatis unde omnis iste<br>natus error sit voluptatem</p><div class="soc"><i></i><i></i><i></i></div></div>
  <div class="member" style="left:836px"><div class="av" role="img" aria-label="Avatar illustration of a team member"></div><h5>TESSA MORROW</h5><p>Sed ut perspiciatis unde omnis iste<br>natus error sit voluptatem</p><div class="soc"><i></i><i></i><i></i></div></div>
</section>

<section class="blog">
  <h2 class="sec-title" style="top:3590px">Latest <span>Blog</span></h2>
  <div class="arrow" style="left:91px;top:3757px">‹</div>
  <div class="arrow" style="left:1079px;top:3757px">›</div>
  <article class="post" style="left:155px"><div class="date"><b>02</b><small>SEP</small></div><h6>Pellentesque faucibus Ut accumsan ultric</h6><p>Duis quam Nam eget lacus Aliquam erat volutpat Quisque dignissim congue leovel lacus vitae felis vestibulum</p><a>READ MORE</a></article>
  <article class="post mid" style="left:461px"><div class="date" style="background:var(--blue)"><b>02</b><small>SEP</small></div><h6>Pellentesque faucibus Ut accumsan ultric</h6><p>Duis quam Nam eget lacus Aliquam erat volutpat Quisque dignissim congue leovel lacus vitae felis vestibulum</p><a>READ MORE</a></article>
  <article class="post" style="left:767px"><div class="date"><b>04</b><small>SEP</small></div><h6>Pellentesque faucibus Ut accumsan ultric</h6><p>Duis quam Nam eget lacus Aliquam erat volutpat Quisque dignissim congue leovel lacus vitae felis vestibulum</p><a>READ MORE</a></article>
</section>

<footer>
  <svg class="abs" style="left:0;top:3940px" width="1200" height="436" aria-hidden="true"><path d="M0 20 Q0 12 40 12 L1200 0 L1200 436 L0 436 Z" fill="var(--footer)"/></svg>
  <div class="abs wordmark" style="left:0;width:1200px;text-align:center;top:4068px;color:#fff;font-size:44px">Tellmark</div>
  <div class="footer-contact">
    <div class="it"><span class="ci"><svg width="12" height="16" viewBox="0 0 12 16"><path d="M6 1a5 5 0 015 5c0 4-5 9-5 9S1 10 1 6a5 5 0 015-5z" fill="none" stroke="#fff" stroke-width="1.6"/><circle cx="6" cy="6" r="1.6" fill="#fff"/></svg></span><span>4410 Harbor Lane<br>Riverton, CA 90417</span></div>
    <div class="it"><span class="ci fill"><svg width="14" height="14" viewBox="0 0 14 14"><path d="M3 1l2.5 3-1.5 1.5a8 8 0 004.5 4.5L10 8.5l3 2.5-1.5 2C6 13 1 8 1 2.5z" fill="#fff"/></svg></span><span>800-555-0172</span></div>
    <div class="it"><span class="ci"><svg width="14" height="10" viewBox="0 0 14 10"><rect x="0.5" y="0.5" width="13" height="9" fill="#fff"/><path d="M1 1l6 4.5L13 1" fill="none" stroke="#151b2d" stroke-width="1.3"/></svg></span><span>hello(at)tellmark.com</span></div>
  </div>
  <nav class="footer-nav"><span>HOME</span><span>SERVICES</span><span>INDUSTRIES</span><span>PRICING</span><span>TEAM</span><span>CONTACT US</span><span>BLOG</span></nav>
  <p class="copy">Copyright 2019 Tellmark All Rights Reserved &nbsp;|&nbsp; Privacy Policy</p>
  <div class="social"><i></i><i style="background:#1fb4e6"></i><i style="background:#1c3f94"></i></div>
</footer>

</body>
</html>
```